Social Media Graphics - Oakline Push REVISED

Create 6-7 individual social media graphics (square size) to encourage folks to join our online course called:

The Harvest Ledger Circle
How to Launch a Multi-Million Business From Scratch
Sign Up Today!

IMPORTANT: Make the largest and most prominent text on the graphic be: How to Launch a Multi-Million Business From Scratch

For the color scheme of the graphics, let's try a blue color palette; make sure the graphics appeal to both men and women

Make sure each graphic contains 1 of the 3 pics attached (crop pic as needed); and make sure one of the graphics is all TEXT only.

Target Market(s)

men and women looking to start a business

Industry/Entity Type

Entrepreneurship

Colors
0054AA
0677BA
7BADD7
CADEEF
E8F1F8

Requirements
Must have
• All the text and use the 3 pics provided; one graphic can be all text; Simple, modern design that's easy to read

```html
<!DOCTYPE html>
<html lang="en">
<head>
<meta charset="utf-8">
<title>The Harvest Ledger Circle – Social Graphics</title>
<link rel="stylesheet" href="https://fonts.googleapis.com/css2?family=Archivo+Black&family=Bebas+Neue&display=swap">
<style>
  :root {
    --page-bg: #0d1828;
    --blue-deep: #0a2a84;
    --blue-mid: #0054aa;
    --blue-bright: #0677ba;
    --blue-sky: #1a9ad8;
    --blue-soft: #7badd7;
    --blue-pale: #cadeef;
    --white: #ffffff;
    --button-fill: #1c2140;
    --button-edge: #b89b5e;
  }
  * { margin: 0; padding: 0; box-sizing: border-box; }
  html, body {
    width: 1200px; height: 400px; overflow: hidden;
    background: var(--page-bg);
  }
  .graphic-row { position: relative; width: 1200px; height: 400px; }
  .graphic {
    position: absolute; top: 11px; width: 378px; height: 378px; overflow: hidden;
    background:
      linear-gradient(155deg, rgba(255,255,255,0.06) 0 30%, transparent 30% 100%),
      linear-gradient(180deg, var(--blue-sky) 0%, var(--blue-bright) 30%, var(--blue-mid) 60%, var(--blue-deep) 100%);
  }
  .graphic--one { left: 10px; }
  .graphic--two { left: 411px; }
  .graphic--three { left: 812px; }

  .graphic__photo { position: absolute; }
  .graphic--one .graphic__photo {
    left: 90px; top: 20px; width: 215px; height: 185px;
    background: linear-gradient(180deg, rgba(60,40,50,0.55) 0%, rgba(200,70,100,0.45) 55%, rgba(6,119,186,0) 100%);
    border-radius: 90px 90px 0 0;
  }
  .graphic--two .graphic__photo {
    left: 0; top: 0; width: 378px; height: 210px;
    background: linear-gradient(180deg, #d9d4cc 0%, #b9bcc2 35%, rgba(123,173,215,0.7) 70%, rgba(0,84,170,0) 100%);
  }
  .graphic--three .graphic__photo {
    left: 75px; top: 20px; width: 230px; height: 185px;
    background: linear-gradient(180deg, rgba(25,30,45,0.6) 0%, rgba(20,50,110,0.55) 55%, rgba(6,119,186,0) 100%);
    border-radius: 90px 90px 0 0;
  }

  .graphic__frame {
    position: absolute; inset: 9px;
    border: 2px solid var(--white);
    pointer-events: none;
  }

  .graphic__content {
    position: absolute; left: 20px; right: 20px; top: 198px;
    text-align: center; color: var(--white);
  }
  .course-name {
    font-family: "Archivo Black", sans-serif;
    font-size: 16px; line-height: 20px; letter-spacing: 0.4px;
  }
  .headline {
    margin-top: 4px;
    font-family: "Bebas Neue", sans-serif;
    font-weight: 400;
    font-size: 39px; line-height: 34px; letter-spacing: 0.3px;
    text-transform: uppercase;
  }
  .cta {
    display: inline-block; margin-top: 8px;
    padding: 0 12px; height: 30px; line-height: 28px;
    background: var(--button-fill);
    border: 2px solid var(--button-edge);
    border-radius: 16px;
    font-family: "Bebas Neue", sans-serif;
    font-size: 21px; color: var(--white);
  }
</style>
</head>
<body>
<main class="graphic-row">
  <section class="graphic graphic--one">
    <div class="graphic__photo" role="img" aria-label="Portrait of the two course hosts smiling, arms crossed"></div>
    <div class="graphic__frame"></div>
    <div class="graphic__content">
      <p class="course-name">THE HARVEST LEDGER CIRCLE</p>
      <h1 class="headline">How to launch a<br>multi-million business<br>from scratch</h1>
      <span class="cta">SIGN UP TODAY!</span>
    </div>
  </section>

  <section class="graphic graphic--two">
    <div class="graphic__photo" role="img" aria-label="The two course hosts speaking on stage with a microphone"></div>
    <div class="graphic__frame"></div>
    <div class="graphic__content">
      <p class="course-name">THE HARVEST LEDGER CIRCLE</p>
      <h1 class="headline">How to launch a<br>multi-million business<br>from scratch</h1>
      <span class="cta">SIGN UP TODAY!</span>
    </div>
  </section>

  <section class="graphic graphic--three">
    <div class="graphic__photo" role="img" aria-label="The two course hosts standing together in dark and denim outfits"></div>
    <div class="graphic__frame"></div>
    <div class="graphic__content">
      <p class="course-name">THE HARVEST LEDGER CIRCLE</p>
      <h1 class="headline">How to launch a<br>multi-million business<br>from scratch</h1>
      <span class="cta">SIGN UP TODAY!</span>
    </div>
  </section>
</main>
</body>
</html>
```